i NEED A MY CURRENT LOGO UPDATED TO MAKE IT LOOK MORE MODERN. I WANT TO KEEP MY CURRENT COLOURS FOR THE LOGO WHICH ARE GREEN, BLACK, WHITE AND SILVER/METALIC COLOURS.

I RUN A BUSINESS WHICH IS CALLED "CONVEYANCING" IN AUSTRALIA. THIS BUSINESS PROVIDES A SERVICES FOR PEOPLE WHO ARE BUYING OR SELLING OR TRANSFER THEIR PROPERTY. WE ARE NOT A REAL ESTATE AGENT. WE PREPARE AND DO ALL WORK NECESSARY TO COMPLETE A LEGAL TRANSFER OF PROPERTY FOR CUSTOMERS. THE REASON i CHOSE THE NAME "BRELMOR CONVEYANCING" IS BECAUSE WE CAN ONLY DO VICTORIAN PROPERTY TRANSFERS AND IN AUSTRALIA THE LAND IS TRANSFERED TO AN OWNER AND WHATEVER IS ON THE LAND BECOMES THE OWNERS.

MY LOGO MUST HAVE THE VICTORIAN STATE AS A SYMBOL (VICTORIA IS ONE OF THE STATES IN AUSTRALIA AND IT'S KNOWN AS A GREEN STATE). I CAN EMAIL YOU THE CURRENT LOGO TO GIVE YOU AN IDEA.

I'M HAPPY WITH THE CURRENT COLOURS BUT NOT THE LAYOUT OR DESIGN. AT THE MOMENT IT'S PRETTY PLAIN AND BORING.

Example - This is a creative design I copied from the net.

Hi All, I've posted a design in which I would like you to consider being creative with the victorian logo as they have done with the swan here.  Just an idea.

Hi All, I just wanted to let you know that other than the colours I requested I want you all to come up with your own idea of the logo.  So far this is the only create design I've seen. 

Target Market(s)

People that are in the market to buy or selling property/real estate.

Industry/Entity Type

Business

Requirements
Must have
• THE COLOURS MUST REMAIN THE SAME AND MUST BE PROFESSIONAL AS WE ARE A PART OF THE LEGAL (PROFESSIONAL)INDUSTRY IN AUSTRALIA
Nice to have
• MUST HAVE THE VICTORIAN LOGO/SYMBOL
Should not have
• SHOULD NOT BE BORING. THE DETAILS OF OUR ADDRESS ON THE ATTACHED IS OLD DETAILS NOT OUR CURRENT DETAILS. IT'S ATTACHED TO SHOW YOU AN EXAMPLE OF THE CURRENT LOGO.

```html
<!DOCTYPE html>
<html lang="en">
<head>
<meta charset="utf-8">
<title>Brelmor Conveyancing – Business Cards</title>
<link rel="stylesheet" href="https://fonts.googleapis.com/css2?family=Roboto:wght@700&family=Roboto+Condensed:wght@700&display=swap">
<style>
  :root {
    --page: #ffffff;
    --card-black: #000000;
    --gloss-dark: #1a1a1a;
    --gloss-mid: #6e6e6e;
    --gloss-light: #f2f2f2;
    --brand-green: #1e9a3c;
    --text-white: #ffffff;
  }
  * { margin: 0; padding: 0; box-sizing: border-box; }
  html, body {
    width: 1200px; height: 819px; overflow: hidden;
    background: var(--page);
  }
  .canvas { position: relative; width: 1200px; height: 819px; }
  .card {
    position: absolute; top: 245px;
    width: 529px; height: 292px;
    border-radius: 26px; overflow: hidden;
    background: var(--card-black);
  }
  .card--back { left: 37px; }
  .card--front { left: 625px; }
  .card__gloss { position: absolute; inset: 0; width: 100%; height: 100%; }

  .disclaimers {
    position: absolute; left: 16px; bottom: 12px;
    list-style: none;
    font-family: "Roboto", Arial, sans-serif;
    font-weight: 700; font-size: 13.5px; line-height: 19px;
    color: var(--text-white);
  }
  .disclaimers li::before { content: "• "; }

  .wordmark {
    position: absolute; left: 0; right: 14px; top: 6px;
    display: flex; align-items: flex-start; justify-content: flex-end; gap: 14px;
    font-family: "Roboto Condensed", "Arial Narrow", sans-serif;
    font-weight: 700; color: var(--brand-green);
    text-align: right;
  }
  .wordmark__square {
    width: 22px; height: 22px; margin-top: 26px;
    background: var(--brand-green);
  }
  .wordmark__name { font-size: 96px; line-height: 96px; letter-spacing: -1px; }
  .wordmark__tag { display: block; font-size: 44px; line-height: 48px; letter-spacing: 0; }

  .holder {
    position: absolute; left: 0; right: 0; top: 190px;
    text-align: center;
    font-family: "Roboto Condensed", "Arial Narrow", sans-serif;
    font-weight: 700; font-size: 29px; letter-spacing: 1px;
    color: var(--brand-green);
  }
  .contact {
    position: absolute; left: 0; right: 0; top: 238px;
    text-align: center;
    font-family: "Roboto Condensed", "Arial Narrow", sans-serif;
    font-weight: 700; font-size: 16px; line-height: 24px;
    color: var(--text-white);
  }
  .contact__value { font-weight: 400; font-family: "Roboto Condensed", "Arial Narrow", sans-serif; }
</style>
</head>
<body>
<main class="canvas">
  <section class="card card--back" aria-label="Business card, reverse side">
    <svg class="card__gloss" viewBox="0 0 529 292" aria-hidden="true">
      <defs>
        <linearGradient id="gloss-back" x1="0" y1="0" x2="1" y2="0.2">
          <stop offset="0" stop-color="var(--gloss-dark)" />
          <stop offset="0.55" stop-color="var(--gloss-mid)" />
          <stop offset="1" stop-color="var(--gloss-light)" />
        </linearGradient>
      </defs>
      <path d="M0 0 H529 V50 C400 40 200 80 0 125 Z" fill="url(#gloss-back)" />
    </svg>
    <ul class="disclaimers">
      <li>This firm holds professional indemnity insurance against civil liability.</li>
      <li>A solicitor is employed by this firm for all legal work.</li>
      <li>Professional Indemnity.</li>
    </ul>
  </section>

  <section class="card card--front" aria-label="Business card, front side">
    <svg class="card__gloss" viewBox="0 0 529 292" aria-hidden="true">
      <defs>
        <linearGradient id="gloss-front" x1="0" y1="0" x2="1" y2="0.2">
          <stop offset="0" stop-color="var(--gloss-dark)" />
          <stop offset="0.55" stop-color="var(--gloss-mid)" />
          <stop offset="1" stop-color="var(--gloss-light)" />
        </linearGradient>
      </defs>
      <path d="M0 0 H529 V50 C400 40 200 80 0 125 Z" fill="url(#gloss-front)" />
    </svg>
    <div class="wordmark">
      <span class="wordmark__square"></span>
      <div class="wordmark__name">BRELMOR<span class="wordmark__tag">Conveyancing</span></div>
    </div>
    <p class="holder">DEFNE ARSLAN</p>
    <p class="contact">
      14 Calder Street, Ashwood Park Victoria; Tel: <span class="contact__value">(03) 9000 4521</span><br>
      Fax: <span class="contact__value">(03) 0000 0000</span>; E-mail: <span class="contact__value">brelmorconveyancing@mailbox.com</span>
    </p>
  </section>
</main>
</body>
</html>
```